Tolvik Commercial Cleaning is lookong for a new business card design.

A fresh new design that's professional and stylish. We need a serious upgrade to our business cards. I have included pictures of our existing ones. Our clients include professional individuals and business owners. We woupdblike something professional and upbeat. Please have fun and see what you come uo with.

Target Market(s)

Property managers, business owners, facility managers and other similar professionals

Industry/Entity Type

Janitorial

Contact Information for Business Card

Name, cell, office number, email, web address

Font styles to use
Sans Serif

Colors

Designer to choose colors to be used in the design.

Requirements
Must have
• please use the green color in our logo
Nice to have
• Bar code
Should not have
• Address

```html
<!DOCTYPE html>
<html lang="en">
<head>
<meta charset="utf-8">
<title>Tolvik Commercial Cleaning — Business Card</title>
<link rel="stylesheet" href="https://fonts.googleapis.com/css2?family=Quicksand:wght@500;700&family=Arimo:wght@400;700&display=swap">
<style>
  :root {
    --stage: #141414;
    --card: #2a2a2a;
    --card-deep: #222222;
    --green: #2fae4e;
    --blue: #3d6aa8;
    --white: #f4f4f4;
    --rule: #e8e8e8;
  }
  * { box-sizing: border-box; margin: 0; padding: 0; }
  html, body { width: 1200px; height: 963px; overflow: hidden; background: var(--stage); }
  .sheet {
    width: 1200px; height: 963px;
    display: flex; flex-direction: column; align-items: center; justify-content: center;
    gap: 40px;
  }
  .card {
    position: relative;
    width: 740px; height: 423px;
    background: var(--card);
    border-radius: 34px;
    border-bottom: 4px solid var(--green);
    overflow: hidden;
  }
  /* front */
  .contact-name {
    position: absolute; left: 56px; top: 226px;
    font-family: "Quicksand", sans-serif; font-weight: 700;
    font-size: 30px; line-height: 1; color: var(--green);
  }
  .contact-rule {
    position: absolute; left: 56px; right: 70px; top: 272px;
    height: 1.5px; background: var(--rule);
  }
  .contact-list {
    position: absolute; left: 56px; top: 290px;
    list-style: none;
    font-family: "Arimo", sans-serif; font-size: 17px; color: var(--white);
  }
  .contact-list li { display: flex; align-items: center; gap: 10px; margin-bottom: 10px; }
  .contact-list svg { width: 16px; height: 16px; flex: none; }
  .brand {
    position: absolute; right: 70px; top: 58px;
    font-family: "Quicksand", sans-serif; font-weight: 700;
  }
  .brand-name { font-size: 96px; line-height: 1; color: var(--green); font-weight: 700; }
  .brand-line { font-size: 22px; color: var(--blue); font-weight: 700; margin-top: 4px; }
  .front-brand { text-align: right; }
  .web {
    position: absolute; right: 70px; top: 240px;
    font-family: "Arimo", sans-serif; font-weight: 700; font-size: 19px; line-height: 1; color: var(--white);
  }
  .web .accent { color: var(--green); }
  /* back */
  .pattern-field {
    position: absolute; inset: 0;
    background: radial-gradient(ellipse at 50% 45%, #2e2e2e 0%, var(--card) 55%, var(--card-deep) 100%);
  }
  .back-brand {
    position: absolute; inset: 0;
    display: flex; flex-direction: column; align-items: center; justify-content: center;
    font-family: "Quicksand", sans-serif; text-align: center;
  }
  .back-brand .brand-name { font-size: 80px; }
  .back-brand .brand-line { font-size: 26px; margin-top: 8px; }
  .tagline { font-size: 24px; font-weight: 500; color: var(--green); margin-top: 4px; }
</style>
</head>
<body>
<main class="sheet">
  <section class="card card-front" aria-label="Business card front">
    <div class="brand front-brand">
      <div class="brand-name">Tolvik</div>
      <div class="brand-line">commercial cleaning</div>
    </div>
    <h1 class="contact-name">dana whitfield</h1>
    <p class="web">www.<span class="accent">tolvikclean</span>.com</p>
    <div class="contact-rule"></div>
    <ul class="contact-list">
      <li>
        <svg viewBox="0 0 24 24" fill="none" stroke="#2fae4e" stroke-width="2" aria-hidden="true"><path d="M5 3h4l2 5-2.5 1.5a11 11 0 0 0 6 6L16 13l5 2v4a2 2 0 0 1-2 2A16 16 0 0 1 3 5a2 2 0 0 1 2-2z"/></svg>
        (555) 014-2270
      </li>
      <li>
        <svg viewBox="0 0 24 24" fill="none" stroke="#2fae4e" stroke-width="2" aria-hidden="true"><rect x="3" y="5" width="18" height="14" rx="1"/><path d="M3 6l9 7 9-7"/></svg>
        dana@tolvikclean.com
      </li>
    </ul>
  </section>

  <section class="card card-back" aria-label="Business card back">
    <div class="pattern-field" role="img" aria-label="Subtle tone-on-tone repeat of the company name across the card"></div>
    <div class="back-brand">
      <div class="brand-name">Tolvik</div>
      <div class="brand-line">commercial cleaning</div>
      <div class="tagline">clean spaces, fresh starts</div>
    </div>
  </section>
</main>
</body>
</html>
```